Business Card Design for BrightvaleMedia.com

--I need a business card design for my company BrightvaleMedia.com

I have attached my logo...I want the brightvale media logo on the front of the business card, and then I want The Quillstone Chief on the back of it with my information.

I would like to see a light colored background as well as a dark colored background

FRONT:
BRIGHTVALE MEDIA LOGO
248 N. Larkmoor
3rd Floor
San Diego CA 92173
www.BrightvaleMedia.com

Advanced Website & App Development
Websites, Apps, Online Voucher Systems

Leading Edge Marketing Services
SMS, VB, SMM, SEM,

BACK:
QUILLSTONE CHIEF LOGO
Dorian Pelletta
The Quillstone Chief
Call Or Text: 619-555-0148
Dorian@QuillstoneChief.example
www.QuillstoneChief.example

Target Market(s)

small business owners

Industry/Entity Type

Business Consultant

Contact Information for Business Card

FRONT:
BRIGHTVALE MEDIA LOGO
248 N. Larkmoor
3rd Floor
San Diego CA 92173
www.BrightvaleMedia.com

SMS, VB, SMM, SEM,

BACK:
QUILLSTONE CHIEF LOGO
Dorian Pelletta
The Quillstone Chief
Dorian@QuillstoneChief.example
www.QuillstoneChief.example

Requirements
Must have
• add this quote on it somewhere, anywhere,preferrably on back
• "The Fastest Way To Success Is To Take Action”
• — Dorian Pelletta, Quillstone Chief
Nice to have
• open
Should not have
• red

```html
<!DOCTYPE html>
<html lang="en">
<head>
<meta charset="utf-8">
<title>Brightvale Media — Business Card</title>
<link rel="stylesheet" href="https://fonts.googleapis.com/css2?family=Source+Sans+3:wght@400&display=swap">
<style>
  :root {
    --stage: #000000;
    --card-dark: #1b1e22;
    --card-dark-band: #1d2a32;
    --card-blue: #1f5473;
    --ink: #ffffff;
    --ink-soft: #e8eef2;
    --ink-muted: rgba(255,255,255,0.75);
    --rule: rgba(255,255,255,0.55);
  }
  * { margin: 0; padding: 0; box-sizing: border-box; }
  html, body {
    width: 1200px; height: 900px; overflow: hidden;
    background: var(--stage);
    font-family: "Source Sans 3", "Myriad Pro", Arial, sans-serif;
    color: var(--ink);
  }
  .canvas { position: relative; width: 1200px; height: 900px; }

  .card {
    position: absolute; top: 271px; width: 457px; height: 281px;
    border-radius: 12px; overflow: hidden;
  }

  /* Back: Quillstone Chief */
  .card--back { left: 137px; background: var(--card-dark); }
  .band { position: absolute; background: var(--card-dark-band); }
  .band--left { left: 0; top: 0; width: 28px; height: 100%; }
  .band--right { left: 354px; top: 0; width: 69px; height: 100%; }
  .band--logo { left: 0; top: 104px; width: 239px; height: 68px; }

  .chief-name {
    position: absolute; left: 20px; top: 119px; width: 208px;
    text-align: right; line-height: 1; font-weight: 400;
  }
  .chief-name__main { display: block; font-size: 25px; letter-spacing: 2px; margin-right: -2px; }
  .chief-name__sub { display: block; font-size: 13px; letter-spacing: 6px; margin-top: 2px; margin-right: -6px; }

  .divider {
    position: absolute; left: 239px; top: 78px; width: 1px; height: 122px;
    background: linear-gradient(to bottom, transparent, var(--rule) 25%, var(--rule) 75%, transparent);
  }

  .person { position: absolute; left: 258px; top: 84px; font-size: 13.5px; line-height: 16px; }

  .contact { position: absolute; left: 258px; top: 150px; list-style: none; font-size: 12.5px; line-height: 14px; }
  .contact li { display: flex; align-items: center; gap: 6px; }
  .contact svg { width: 9px; height: 9px; flex: none; fill: var(--ink); }

  .quote {
    position: absolute; left: 28px; top: 214px; width: 200px;
    text-align: right; font-size: 11px; line-height: 14px; color: var(--ink-muted);
  }
  .quote__by { display: block; margin-top: 3px; font-size: 10px; }

  /* Front: Brightvale Media */
  .card--front { left: 626px; background: var(--card-blue); text-align: center; }
  .brand { position: absolute; left: 67px; width: 323px; top: 27px; }
  .brand__name { font-size: 40px; letter-spacing: 5px; margin-right: -5px; line-height: 40px; font-weight: 400; }
  .brand__tag {
    display: flex; align-items: center; gap: 8px;
    margin-top: 2px; font-size: 16px; letter-spacing: 5px; line-height: 18px;
  }
  .brand__tag::before, .brand__tag::after {
    content: ""; flex: 1; height: 1px; background: var(--ink-soft);
  }
  .brand__tag::after { margin-left: -5px; }
  .front-line { position: absolute; left: 0; right: 0; font-size: 13px; line-height: 17px; }
  .front-line--address { top: 102px; }
  .front-line--dev { top: 140px; }
  .front-line--marketing { top: 189px; line-height: 19px; }
  .front-line--web { top: 242px; }
</style>
</head>
<body>
<main class="canvas">

  <section class="card card--back" aria-label="Quillstone Chief card">
    <div class="band band--left"></div>
    <div class="band band--right"></div>
    <div class="band band--logo"></div>

    <div class="chief-name">
      <span class="chief-name__main">QUILLSTONE</span>
      <span class="chief-name__sub">CHIEF</span>
    </div>

    <div class="divider"></div>

    <div class="person">
      <p>Dorian Pelletta</p>
      <p>The Quillstone Chief</p>
    </div>

    <ul class="contact">
      <li>
        <svg viewBox="0 0 10 10" aria-hidden="true"><path d="M1 3.5C1 2 2.5 1.5 5 1.5S9 2 9 3.5L7.5 4.3 6.8 3H3.2L2.5 4.3ZM2.6 5h4.8l.8 3.5H1.8Z"/></svg>
        <span>619-555-0148</span>
      </li>
      <li>
        <svg viewBox="0 0 10 10" aria-hidden="true"><path d="M1 2h8v6H1Z M1.6 2.6 5 5.4 8.4 2.6" fill="var(--ink)" stroke="var(--card-dark)" stroke-width="0.8"/></svg>
        <span>Dorian@QuillstoneChief.example</span>
      </li>
      <li>
        <svg viewBox="0 0 10 10" aria-hidden="true"><circle cx="5" cy="5" r="4.2"/><path d="M3 3.5 4.5 3 5 4.5 3.8 5.5ZM6 6l1.5-.5.3 1.5L6.5 7.8Z" fill="var(--card-dark)"/></svg>
        <span>www.QuillstoneChief.example</span>
      </li>
    </ul>

    <blockquote class="quote">
      <p>“The Fastest Way To Success<br>Is To Take Action”</p>
      <span class="quote__by">— Dorian Pelletta, Quillstone Chief</span>
    </blockquote>
  </section>

  <section class="card card--front" aria-label="Brightvale Media card">
    <div class="brand">
      <p class="brand__name">BRIGHTVALE</p>
      <p class="brand__tag">MEDIA</p>
    </div>
    <p class="front-line front-line--address">248 N. Larkmoor, 3rd Floor, San Diego CA 92173</p>
    <p class="front-line front-line--dev">Advanced Website &amp; App Development<br>Websites, Apps, Online Voucher Systems</p>
    <p class="front-line front-line--marketing">Leading Edge Marketing Services<br>SMS | VB | SMM | SEM</p>
    <p class="front-line front-line--web">www.BrightvaleMedia.com</p>
  </section>

</main>
</body>
</html>
```